International Clinical Software Company needs a new business card design

We are looking for a new business card design for our company that has recently expanded into the UK market, making us a multinational company.
After having rebranded our website and produced a new style guide, we are looking for a business card that is creative and attention grabbing, while being consistent with the style and colour scheme used on the new website, www.plumvora.example
We produce care management technology for the aged care market, but the main aspect we aim to communicate is the human element of our software, and the way it assists in providing better care for aged people, and stronger relationships between aged people and the staff that care for them.
Our current business card is a dark green with gold text, which makes the text quite difficult to read, not very aesthetically appealing and the colour scheme looks quite dated.
We would like something fresh and modern, that can still be colourful but doesn't use large blocks of dark colour, and uses the colours within our logo.
Something tying in with the leaves that are used in our logo could work quite nicely, along with the Autumn/Fall colours of soft greens, yellows and reds (also in our existing logo). However also happy to look at fresh, completely out of the box ideas we may not have yet considered.
Target Market(s)
The people that receive this business card work in the aged card or health industry and are either corporate/management level staff or clinical (Registered Nurses, care workers etc.)
Industry/Entity Type
Health Product
Contact Information for Business Card
Company Name - BrindlewayCare
Company locations: United Kingdom, Australia, New Zealand
Staff Details:
Staff name: Derek Mallow
Staff job title: Executive Chairman
Staff email: d.mallow@plumvora.example
Office phone number: 01742 918576
Font styles to use
Other font styles liked:
- Calibri
Requirements
Must have
- Must include the BrindlewayCare brand name in it's current font
- Must include logo (3 leaves in gold circle)
- Must include Business Card Details
Nice to have
- Elements of gold
- White space
- Something autumn themed but not too cliched
Should not have
- No blue - used by a major competitor and we would like to differentiate from them
- Large blocks of dark green colour (the green that appears in our leaves on the logo on our current business card is the background colour and it is far too dark)

```html
<!DOCTYPE html>
<html lang="en">
<head>
<meta charset="utf-8">
<title>BrindlewayCare Business Card</title>
<link href="https://fonts.googleapis.com/css2?family=Source+Sans+3:wght@400;600&display=swap" rel="stylesheet">
<style>
  :root {
    --backdrop: #141414;
    --card: #ffffff;
    --gold: #b39a6b;
    --ink: #5f5f5f;
    --tone-yellow: #eccb4a;
    --tone-orange: #e6a24a;
    --tone-red: #d4714f;
  }
  * { margin: 0; padding: 0; box-sizing: border-box; }
  html, body {
    width: 1200px; height: 900px; overflow: hidden;
    background: var(--backdrop);
    font-family: "Source Sans 3", "Calibri", sans-serif;
  }
  .canvas { position: relative; width: 1200px; height: 900px; }
  .card {
    position: absolute; top: 170px; width: 347px; height: 560px;
    background: var(--card); overflow: hidden;
  }
  .card--front { left: 259px; }
  .card--back { left: 631px; }

  .leaf-band {
    position: absolute; top: 0; width: 116px; height: 560px;
    background: linear-gradient(180deg, var(--tone-yellow) 0%, var(--tone-orange) 45%, var(--tone-red) 100%);
  }
  .card--front .leaf-band { right: 0; }
  .card--back .leaf-band { left: 0; }

  .brand-mark { position: absolute; color: var(--gold); }
  .brand-mark__dot { display: block; border-radius: 50%; background: var(--gold); flex: none; }

  .card--front .brand-mark {
    left: 34px; top: 176px; display: flex; align-items: center; gap: 8px;
    font-size: 18px; font-weight: 600;
  }
  .card--front .brand-mark__dot { width: 22px; height: 22px; }

  .card--back .brand-mark {
    left: 99px; top: 347px; width: 240px;
    display: flex; flex-direction: column; align-items: center; gap: 8px;
    font-size: 30px; font-weight: 400; line-height: 40px;
  }
  .card--back .brand-mark__dot { width: 80px; height: 80px; }

  .contact { position: absolute; left: 35px; top: 343px; color: var(--ink); font-size: 15px; line-height: 20px; }
  .contact__name { color: var(--gold); font-weight: 600; font-size: 19px; line-height: 22px; }
  .contact__role { margin-bottom: 15px; }
  .contact__email { display: flex; align-items: center; gap: 4px; margin-bottom: 16px; font-size: 13.5px; }
  .contact__email svg { width: 12px; height: 12px; fill: var(--gold); }
</style>
</head>
<body>
<main class="canvas">
  <section class="card card--front">
    <div class="brand-mark">
      <span class="brand-mark__dot"></span>
      <span class="brand-mark__name">BrindlewayCare</span>
    </div>
    <div class="contact">
      <p class="contact__name">Derek Mallow</p>
      <p class="contact__role">Executive Chairman</p>
      <p class="contact__email">
        <svg viewBox="0 0 24 24" aria-hidden="true"><path d="M6.6 10.8a15.2 15.2 0 0 0 6.6 6.6l2.2-2.2a1 1 0 0 1 1-.25 11.4 11.4 0 0 0 3.6.57 1 1 0 0 1 1 1V20a1 1 0 0 1-1 1A17 17 0 0 1 3 4a1 1 0 0 1 1-1h3.5a1 1 0 0 1 1 1 11.4 11.4 0 0 0 .57 3.6 1 1 0 0 1-.25 1z"/></svg>
        d.mallow@plumvora.example
      </p>
      <p>United Kingdom, Australia</p>
      <p>New Zealand</p>
    </div>
    <div class="leaf-band" role="img" aria-label="Illustration of falling autumn leaves"></div>
  </section>

  <section class="card card--back">
    <div class="leaf-band" role="img" aria-label="Illustration of falling autumn leaves"></div>
    <div class="brand-mark">
      <span class="brand-mark__dot"></span>
      <span class="brand-mark__name">BrindlewayCare</span>
    </div>
  </section>
</main>
</body>
</html>
```